Business Cards for IT Consulting Company (Managed Service Provider)

I am looking to have some business cards printed and would like some designs. We are an IT Consulting company based in Vancouver BC. I would like a nice clean and modern look to the cards. I have uploaded all the versions of my logo so parts can be used as needed. Here is a snippit from our website homepage:

Quillbrook Networks Ltd. is an IT Solutions Partner located in Vancouver BC, Canada. We offer IT solutions and support to customers in the greater Vancouver Area. With expertise in Microsoft platforms, as well as Linux and Mac OSX and over 12 years experience in the IT industry, Quillbrook Networks is dedicated to offering our clients top quality service and products. We take pride in the solutions we offer our customers. The greatest compliment a client can give us is to recommend our services.

Quillbrook Networks Ltd. offers a wide range of IT services from onsite service to remote support and managed service solutions. This allows clients to choose the support path that best suits their company’s needs. Supporting many different sized companies from small to enterprise level over the past 12 years Quillbrook Networks has the experience and expertise needed to ensure things run smoothly. Allowing our clients to focus on doing business.

Revolutionizing the way IT services are delivered.

Quillbrook Networks is dedicated to providing our clients with IT solutions that work and grow with them for years to come. This philosophy helps save money in the long run instead of replacing equipment constantly. Far too often IT solutions are not well thought out and while possibly solving the problem at hand, require replacement due to growth or quality within a very short time frame. Quillbrook Networks takes pride in providing solutions that will last and be able to accommodate growth without the need for replacement.

Industry/Entity Type

Information Technology

Contact Information for Business Card

Quillbrook Networks Ltd.
(Employee Name)
Eml: (Employees Email Address)
Web: quillbrook.me
Ph: 604-555-0148

Font styles to use
Serif
Sans Serif

Requirements
Must have
• The Company logo and company colors.
Nice to have
• - Our tag line: "Revolutionizing IT Services" or "Revolutionizing the way IT services are delivered."
• - Also I really like the idea of nature and technology together blending which is sort of where my logo came from so integrating that somehow onto the business cards would be great.

```html
<!DOCTYPE html>
<html lang="en">
<head>
<meta charset="utf-8">
<title>Quillbrook Networks Ltd. — Business Card</title>
<link rel="stylesheet" href="https://fonts.googleapis.com/css2?family=Source+Sans+3:wght@400;600&display=swap">
<style>
  :root {
    --backdrop: #8c8d8f;
    --card-front: #e9eaec;
    --brand-blue: #1a93d3;
    --back-blue: #1b8fcc;
    --band-dark: #4a4b4e;
    --text-grey: #4f5054;
    --divider: #b9babd;
    --white: #ffffff;
  }
  * { margin: 0; padding: 0; box-sizing: border-box; }
  html, body {
    width: 1105px; height: 1200px; overflow: hidden;
    background: var(--backdrop);
    font-family: "Source Sans 3", "Segoe UI", sans-serif;
  }
  .canvas { position: relative; width: 1105px; height: 1200px; }
  .card {
    position: absolute; left: 178px; width: 748px; height: 427px; overflow: hidden;
  }
  .card-front { top: 119px; background: var(--card-front); }
  .card-back { top: 640px; background: var(--back-blue); }

  .brand { position: absolute; display: flex; align-items: center; gap: 14px; }
  .brand-dot { border-radius: 50%; flex: none; }
  .brand-name { font-weight: 600; line-height: 0.95; }
  .brand-name small { display: block; letter-spacing: 0.06em; line-height: 1.2; }

  .card-front .brand { left: 58px; top: 160px; color: var(--brand-blue); }
  .card-front .brand-dot { width: 52px; height: 52px; border: 4px solid var(--brand-blue); }
  .card-front .brand-name { font-size: 46px; }
  .card-front .brand-name small { font-size: 17px; }

  .divider { position: absolute; left: 413px; top: 109px; width: 1px; height: 193px; background: var(--divider); }

  .contact { position: absolute; left: 446px; top: 96px; color: var(--text-grey); font-size: 19px; }
  .contact-name { color: var(--brand-blue); font-size: 31px; font-weight: 600; margin-bottom: 16px; }
  .contact-address { line-height: 28px; margin-bottom: 10px; }
  .contact-line { display: flex; align-items: center; gap: 10px; height: 28px; }
  .contact-line svg { width: 18px; height: 18px; flex: none; }

  .bottom-bands { position: absolute; left: 0; top: 0; width: 748px; height: 427px; }
  .tagline {
    position: absolute; left: 430px; right: 0; top: 392px; text-align: center;
    color: var(--white); font-size: 21px; font-weight: 600;
  }

  .card-back .brand { left: 0; right: 0; top: 150px; justify-content: center; color: var(--white); gap: 20px; }
  .card-back .brand-dot { width: 72px; height: 72px; border: 4px solid var(--white); }
  .card-back .brand-name { font-size: 66px; }
  .card-back .brand-name small { font-size: 25px; }
</style>
</head>
<body>
<main class="canvas">
  <section class="card card-front" aria-label="Business card front">
    <div class="brand">
      <span class="brand-dot"></span>
      <div class="brand-name">quillbrook<small>NETWORKS LTD.</small></div>
    </div>

    <div class="divider"></div>

    <div class="contact">
      <div class="contact-name">Dana Whitfield</div>
      <div class="contact-address">2210 Cedarvale Road<br>Vancouver, BC V5K 0A1</div>
      <div class="contact-line">
        <svg viewBox="0 0 20 20" aria-hidden="true"><path fill="#1a93d3" d="M5 2l3 4-2 2c1 2.5 3.5 5 6 6l2-2 4 3-2 3C9 18 2 11 2 4z"/></svg>
        604-555-0148
      </div>
      <div class="contact-line">
        <svg viewBox="0 0 20 20" aria-hidden="true"><rect x="2" y="5" width="16" height="11" fill="#1a93d3"/><path d="M2 5l8 6 8-6" fill="none" stroke="#e9eaec" stroke-width="1.5"/></svg>
        dwhitfield@quillbrook.me
      </div>
      <div class="contact-line">
        <svg viewBox="0 0 20 20" aria-hidden="true"><circle cx="10" cy="10" r="8" fill="#1a93d3"/><path d="M2 10h16M10 2c3 3 3 13 0 16M10 2c-3 3-3 13 0 16" fill="none" stroke="#e9eaec" stroke-width="1.2"/></svg>
        www.quillbrook.me
      </div>
    </div>

    <svg class="bottom-bands" viewBox="0 0 748 427" aria-hidden="true">
      <polygon points="0,404 400,404 378,427 0,427" fill="var(--brand-blue)"/>
      <polygon points="421,389 748,389 748,427 385,427" fill="var(--band-dark)"/>
    </svg>
    <div class="tagline">Revolutionizing IT Services</div>
  </section>

  <section class="card card-back" aria-label="Business card back">
    <div class="brand">
      <span class="brand-dot"></span>
      <div class="brand-name">quillbrook<small>NETWORKS LTD.</small></div>
    </div>
  </section>
</main>
</body>
</html>
```